Harbor Crestline (Business Card Design)

Need business cards designed. Something modern, chic, and sleek. Mabye the back of the card should be the navy blue that is in the logo and then just the logo on the back.

Target Market(s)

Those in the hotel, office, and renovation industry

Contact Information for Business Card

1. Logo 2. Dorian Fenwick 3. CEO/Founder 4. Phone: (833) HarbCre / (833) 427-2731 5. Email: dorian@theharborcrestline.com 6. Website: www.theharborcrestline.com

Font styles to use
Other font styles liked:
• Look at the logo font and base the font for everything else off of that.

Colors
0054AA
0677BA
7BADD7
CADEEF
E8F1F8

Requirements
Must have
• Colors that are associated in the logo
Nice to have
• Sleek modern clean and chic design.

```html
<!DOCTYPE html>
<html lang="en">
<head>
<meta charset="utf-8">
<title>Harbor Crestline – Business Card</title>
<link rel="stylesheet" href="https://fonts.googleapis.com/css2?family=Montserrat:wght@500;600;700&family=Open+Sans:wght@400;600&display=swap">
<style>
  :root {
    --backdrop: #2b2b2e;
    --navy: #0c1848;
    --navy-deep: #081236;
    --navy-glow: #3a3d7a;
    --white: #ffffff;
    --gold: #c9a13b;
    --soft: #dfe3ee;
  }
  * { box-sizing: border-box; margin: 0; padding: 0; }
  html, body { width: 1200px; height: 780px; overflow: hidden; }
  body {
    background: var(--backdrop);
    font-family: "Open Sans", Arial, sans-serif;
    position: relative;
  }
  .card {
    position: absolute;
    top: 235px;
    width: 540px;
    height: 309px;
    background: var(--navy);
    border-radius: 3px;
    overflow: hidden;
  }
  .card--front { left: 40px; }
  .card--back { left: 620px; }

  /* front */
  .brand-panel {
    position: absolute;
    left: 40px; top: 64px;
    width: 170px; height: 170px;
    background: linear-gradient(90deg, var(--navy-deep) 0%, var(--navy-deep) 45%, var(--navy-glow) 100%);
  }
  .accent-bar {
    position: absolute;
    right: 0; top: 178px;
    width: 14px; height: 42px;
    background: var(--gold);
  }
  .front-content {
    position: absolute;
    right: 34px; top: 30px;
    width: 300px;
    text-align: right;
  }
  .wordmark {
    display: flex;
    align-items: center;
    justify-content: flex-end;
    gap: 10px;
    font-family: "Montserrat", Arial, sans-serif;
    font-weight: 600;
    color: var(--white);
    text-transform: uppercase;
    letter-spacing: 2px;
  }
  .wordmark__square { background: var(--white); flex: none; }
  .front-content .wordmark { font-size: 17px; }
  .front-content .wordmark__square { width: 14px; height: 14px; }
  .person-name {
    margin-top: 22px;
    font-family: "Montserrat", Arial, sans-serif;
    font-weight: 700;
    font-size: 27px;
    color: var(--gold);
    line-height: 1.1;
  }
  .person-role {
    font-size: 13px;
    color: var(--white);
    margin-top: 4px;
  }
  .contact-list {
    list-style: none;
    margin-top: 16px;
    font-size: 11.5px;
    line-height: 1.6;
    color: var(--soft);
  }
  .contact-list li { display: flex; justify-content: flex-end; align-items: center; gap: 6px; }
  .contact-list .icon { width: 11px; height: 11px; flex: none; }
  .contact-list .icon-spacer { width: 11px; flex: none; }

  /* back */
  .card--back .wordmark {
    position: absolute;
    inset: 0;
    justify-content: center;
    font-size: 26px;
    letter-spacing: 4px;
  }
  .card--back .wordmark__square { width: 22px; height: 22px; }
</style>
</head>
<body>

<section class="card card--front" aria-label="Business card front">
  <div class="brand-panel" role="img" aria-label="Large tonal brand square"></div>
  <div class="accent-bar"></div>
  <div class="front-content">
    <div class="wordmark"><span class="wordmark__square"></span>Harbor Crestline</div>
    <p class="person-name">Dorian Fenwick</p>
    <p class="person-role">CEO/Founder</p>
    <ul class="contact-list">
      <li>4120 Linden Park Rd<span class="icon-spacer"></span></li>
      <li>Suite 210, Easton, MD 21601<span class="icon-spacer"></span></li>
      <li>(833) HarbCre / (833) 427-2731
        <svg class="icon" viewBox="0 0 24 24" aria-hidden="true"><path fill="#c9a13b" d="M6.6 10.8a15.1 15.1 0 0 0 6.6 6.6l2.2-2.2a1 1 0 0 1 1-.25 11.4 11.4 0 0 0 3.6.57 1 1 0 0 1 1 1V20a1 1 0 0 1-1 1A17 17 0 0 1 3 4a1 1 0 0 1 1-1h3.5a1 1 0 0 1 1 1c0 1.25.2 2.45.57 3.57a1 1 0 0 1-.25 1z"/></svg>
      </li>
      <li>www.theharborcrestline.com
        <svg class="icon" viewBox="0 0 24 24" aria-hidden="true"><circle cx="12" cy="12" r="9" fill="none" stroke="#c9a13b" stroke-width="2.4"/><path d="M3 12h18M12 3c3 3 3 15 0 18M12 3c-3 3-3 15 0 18" fill="none" stroke="#c9a13b" stroke-width="1.8"/></svg>
      </li>
      <li>dorian@theharborcrestline.com
        <svg class="icon" viewBox="0 0 24 24" aria-hidden="true"><rect x="2" y="5" width="20" height="14" rx="1.5" fill="#c9a13b"/><path d="M3 6l9 7 9-7" fill="none" stroke="#0c1848" stroke-width="1.8"/></svg>
      </li>
    </ul>
  </div>
</section>

<section class="card card--back" aria-label="Business card back">
  <div class="wordmark"><span class="wordmark__square"></span>Harbor Crestline</div>
</section>

</body>
</html>
```